Tollin Waste Website Design

Our new start-up needs a website design. We plan to help businesses find more sustainable ways to manage their waste. Our initial website aims to gather contact data from potential business customers and comprehensive information from waste facilities and waste transporters. We have a logo design (attached) which we would like included in the website design. I have also attached a number of pages that describe what information should appear on each page as well as a web design brief file that describes the look we are after.

```html
<!DOCTYPE html>
<html lang="en">
<head>
<meta charset="utf-8">
<title>Tollin Waste — Website Design</title>
<link href="https://fonts.googleapis.com/css2?family=Lato:wght@400;700;900&display=swap" rel="stylesheet">
<style>
  :root {
    --bg-light: #9cc92a;
    --bg-dark: #5c9a26;
    --lime: #9bcb2c;
    --lime-deep: #7db220;
    --ink: #ffffff;
    --ink-soft: #d8d8d8;
    --panel-dark: #232323;
    --footer: #3a3a3a;
    --circle-fill: rgba(32, 32, 32, 0.9);
  }
  * { box-sizing: border-box; margin: 0; padding: 0; }
  html, body { width: 1200px; height: 427px; overflow: hidden; }
  body {
    font-family: "Lato", Arial, sans-serif;
    background: linear-gradient(180deg, var(--bg-light) 0%, var(--bg-dark) 100%);
    position: relative;
  }
  .screen {
    position: absolute; top: 30px; width: 566px; height: 368px; overflow: hidden;
  }
  .screen--home { left: 29px; }
  .screen--signup { left: 609px; }

  .hero-photo {
    position: absolute; inset: 0;
    background:
      radial-gradient(ellipse at 60% 70%, #8a6a2a 0%, rgba(120,90,40,0) 45%),
      linear-gradient(180deg, #2f3a22 0%, #4b5a34 45%, #555048 75%, #3a3a38 100%);
  }
  .hero-shade { position: absolute; inset: 0; background: rgba(20, 22, 18, 0.55); }

  .nav {
    position: absolute; top: 48px; left: 0; width: 100%; height: 26px;
    font-size: 7.5px; font-weight: 700; color: var(--ink); letter-spacing: 0.2px;
  }
  .nav a { position: absolute; top: 9px; color: inherit; text-decoration: none; }
  .brand {
    position: absolute; left: 224px; top: 2px; display: flex; align-items: center; gap: 5px;
    font-size: 17px; font-weight: 900; color: var(--ink); letter-spacing: 0.5px; white-space: nowrap;
  }
  .brand-dot { width: 20px; height: 20px; border-radius: 50%; border: 3px solid var(--lime); }

  .hero-title {
    position: absolute; top: 119px; width: 100%; text-align: center;
    font-size: 23px; font-weight: 900; color: var(--lime); letter-spacing: 1px;
  }
  .hero-sub {
    position: absolute; top: 147px; width: 100%; text-align: center;
    font-size: 13px; font-weight: 700; color: var(--ink);
  }

  .role-circle { position: absolute; top: 175px; width: 116px; height: 116px; }
  .role-circle svg { position: absolute; inset: 0; }
  .role-label {
    position: absolute; top: 56px; width: 100%; text-align: center; color: var(--ink);
    font-size: 8.5px; letter-spacing: 1.5px; line-height: 1.2;
  }
  .role-label strong { display: block; font-size: 10px; font-weight: 900; letter-spacing: 0.3px; }

  .footer {
    position: absolute; left: 0; bottom: 0; width: 100%; height: 32px; background: var(--footer);
    font-size: 6px; color: var(--ink-soft); text-align: center; line-height: 32px;
  }

  .modal-shade { position: absolute; inset: 0; background: rgba(22, 22, 22, 0.9); }
  .modal-brand {
    position: absolute; top: 70px; width: 100%; display: flex; justify-content: center; align-items: center; gap: 6px;
    font-size: 12px; font-weight: 900; color: var(--lime);
  }
  .modal-brand .brand-dot { width: 22px; height: 22px; }
  .modal-title {
    position: absolute; top: 107px; width: 100%; text-align: center;
    font-size: 22px; font-weight: 900; color: var(--ink);
  }
  .modal-text {
    position: absolute; top: 140px; left: 100px; width: 366px; text-align: center;
    font-size: 14px; line-height: 19px; color: var(--ink);
  }
  .signup-form {
    position: absolute; top: 190px; left: 136px; width: 311px; height: 30px;
    border: 1px solid #e6e6e6; border-radius: 15px; display: flex; align-items: center;
  }
  .signup-form svg { margin-left: 13px; }
  .signup-input {
    margin-left: 8px; font-size: 9.5px; color: #e6e6e6; flex: 1;
  }
  .signup-button {
    margin-right: 4px; width: 72px; height: 22px; border-radius: 11px; background: var(--lime);
    color: var(--ink); font-size: 9px; font-weight: 900; text-align: center; line-height: 22px;
  }
</style>
</head>
<body>

<section class="screen screen--home">
  <div class="hero-photo" role="img" aria-label="Photo of a waste collection truck on a tree-lined street"></div>
  <div class="hero-shade"></div>
  <nav class="nav">
    <a style="left:90px">ABOUT US</a>
    <a style="left:143px">WHAT WE DO</a>
    <span class="brand"><span class="brand-dot"></span>Tollin Waste</span>
    <a style="left:367px">RESOURCES</a>
    <a style="left:425px">CONTACT US</a>
  </nav>
  <h1 class="hero-title">WELCOME TO TOLLIN WASTE</h1>
  <p class="hero-sub">TAKE CONTROL OF YOUR WASTE HERE:</p>

  <div class="role-circle" style="left:97px">
    <svg viewBox="0 0 116 116" width="116" height="116">
      <circle cx="58" cy="58" r="52" fill="var(--circle-fill)"/>
      <path d="M58 6 A52 52 0 1 0 110 58" fill="none" stroke="var(--lime)" stroke-width="7"/>
      <g fill="none" stroke="#fff" stroke-width="1.2"><rect x="49" y="28" width="11" height="16"/><circle cx="65" cy="38" r="6"/></g>
      <circle cx="58" cy="91" r="8" fill="var(--lime-deep)"/>
      <path d="M54 89 L58 93 L62 89" fill="none" stroke="#fff" stroke-width="1.6"/>
    </svg>
    <div class="role-label">WASTE<strong>PRODUCERS</strong></div>
  </div>

  <div class="role-circle" style="left:221px">
    <svg viewBox="0 0 116 116" width="116" height="116">
      <circle cx="58" cy="58" r="52" fill="var(--circle-fill)"/>
      <path d="M58 6 A52 52 0 1 0 110 58" fill="none" stroke="var(--lime)" stroke-width="7"/>
      <g fill="none" stroke="#fff" stroke-width="1.2"><rect x="45" y="30" width="8" height="13"/><rect x="54" y="30" width="8" height="13"/><rect x="63" y="30" width="8" height="13"/></g>
      <circle cx="58" cy="91" r="8" fill="var(--lime-deep)"/>
      <path d="M54 89 L58 93 L62 89" fill="none" stroke="#fff" stroke-width="1.6"/>
    </svg>
    <div class="role-label">WASTE<strong>FACILITIES</strong></div>
  </div>

  <div class="role-circle" style="left:345px">
    <svg viewBox="0 0 116 116" width="116" height="116">
      <circle cx="58" cy="58" r="52" fill="var(--circle-fill)"/>
      <path d="M58 6 A52 52 0 1 0 110 58" fill="none" stroke="var(--lime)" stroke-width="7"/>
      <g fill="none" stroke="#fff" stroke-width="1.2"><rect x="44" y="30" width="18" height="12"/><path d="M62 34 H68 L72 38 V42 H62"/><circle cx="49" cy="44" r="2"/><circle cx="67" cy="44" r="2"/></g>
      <circle cx="58" cy="91" r="8" fill="var(--lime-deep)"/>
      <path d="M54 89 L58 93 L62 89" fill="none" stroke="#fff" stroke-width="1.6"/>
    </svg>
    <div class="role-label">WASTE<strong>TRANSPORTERS</strong></div>
  </div>

  <footer class="footer">© 2018 Company Name All right reserved Term of Use</footer>
</section>

<section class="screen screen--signup">
  <div class="hero-photo" role="img" aria-label="Dimmed photo of a waste collection truck behind the sign-up window"></div>
  <div class="modal-shade"></div>
  <div class="modal-brand"><span class="brand-dot"></span>Tollin Waste</div>
  <h2 class="modal-title">WELCOME TO TOLLIN WASTE</h2>
  <p class="modal-text">We are just getting started. Please register your email address to receive updates from us.</p>
  <div class="signup-form">
    <svg width="13" height="10" viewBox="0 0 13 10"><rect x="0.5" y="0.5" width="12" height="9" fill="none" stroke="#ddd"/><path d="M0.5 0.5 L6.5 5.5 L12.5 0.5" fill="none" stroke="#ddd"/></svg>
    <span class="signup-input">Email address</span>
    <span class="signup-button">SIGN UP</span>
  </div>
</section>

</body>
</html>
```